Consultancy Business Card Design

We need a business card design for a new company based in singapore called KestrelOak. KestrelOak a boutique consultancy firm offering broad-based business solutions, from conception to re-invention, for ventures from new start-ups to long-running traditional businesses.
Its 2 main divisions (Food & Beverage Operations and Construction & Project Management) have access to a wide range of networks, knowledge bases, and resources to service its clients across numerous diverse sectors. This includes, and is not limited to, construction, F&B, and retail.
We are a company that combines the ambition, boldness and energy of one in the 20s with the dedication, level-headedness and dependability of one entering its 30s. Bridging the experiences of the old with ideals of the young, we draw on the positives of both to create a unique synergy.
We hope to see designs that fits our company profile.
Industry/Entity Type
Boutique
Contact Information for Business Card
KestrelOak(Company Name)
Marcus Thiel (Name)
Principle Consultant (Title)
F&B and Hospitality (Division)
(+65) 8043 5617 (Contact no.)
marcus@kestreloak.com.sg (Email)
Colors
Designer to choose colors to be used in the design.

```html
<!DOCTYPE html>
<html lang="en">
<head>
<meta charset="UTF-8">
<title>KestrelOak Business Card</title>
<link href="https://fonts.googleapis.com/css2?family=Montserrat:wght@500;600&display=swap" rel="stylesheet">
<style>
  :root {
    --backdrop: #2b2b2d;
    --card-red: #dc2227;
    --card-red-light: #e84e55;
    --card-red-deep: #c4161c;
    --paper-white: #f4f4f2;
    --ink-dark: #1c1c1c;
    --text-light: #ffffff;
  }
  * { margin: 0; padding: 0; box-sizing: border-box; }
  html, body {
    width: 1200px;
    height: 900px;
    overflow: hidden;
    background: var(--backdrop);
    font-family: "Montserrat", Arial, sans-serif;
  }
  .stage {
    width: 1200px;
    height: 900px;
    display: flex;
    justify-content: center;
    align-items: center;
    gap: 80px;
  }
  .card {
    width: 380px;
    height: 665px;
    display: flex;
    flex-direction: column;
    overflow: hidden;
    box-shadow: 0 12px 30px rgba(0,0,0,0.45);
  }
  .card-red-field {
    flex: 1;
    background:
      radial-gradient(ellipse at 55% 40%, var(--card-red-light) 0%, rgba(232,78,85,0) 60%),
      linear-gradient(160deg, var(--card-red) 0%, var(--card-red-deep) 100%);
  }
  .logo-band {
    background: var(--paper-white);
    display: flex;
    align-items: center;
  }
  .brand-name {
    font-weight: 600;
    color: var(--ink-dark);
    letter-spacing: -0.5px;
  }

  /* Contact side */
  .card-contact .logo-band {
    height: 160px;
    padding-left: 26px;
  }
  .card-contact .brand-name { font-size: 44px; }
  .contact-list {
    display: flex;
    flex-direction: column;
    align-items: center;
    padding-top: 70px;
    gap: 52px;
    color: var(--text-light);
    text-align: center;
  }
  .contact-item {
    display: flex;
    flex-direction: column;
    align-items: center;
    gap: 16px;
  }
  .contact-icon {
    width: 34px;
    height: 34px;
    border: 2px solid var(--text-light);
    display: flex;
    align-items: center;
    justify-content: center;
  }
  .contact-icon svg { width: 20px; height: 20px; fill: var(--text-light); }
  .contact-text {
    font-size: 13px;
    font-weight: 500;
    line-height: 1.45;
  }

  /* Logo side */
  .card-front .logo-band {
    height: 190px;
    justify-content: center;
  }
  .card-front .brand-name { font-size: 50px; }
</style>
</head>
<body>
  <main class="stage">
    <section class="card card-contact">
      <div class="logo-band">
        <span class="brand-name">KestrelOak</span>
      </div>
      <div class="card-red-field">
        <div class="contact-list">
          <div class="contact-item">
            <span class="contact-icon">
              <svg viewBox="0 0 20 20" aria-hidden="true"><circle cx="10" cy="6.5" r="4"/><path d="M2 19c0-5 3.6-7.5 8-7.5s8 2.5 8 7.5z"/></svg>
            </span>
            <p class="contact-text">Marcus Thiel<br>- Principle Consultant -<br>F&amp;B and Hospitality</p>
          </div>
          <div class="contact-item">
            <span class="contact-icon">
              <svg viewBox="0 0 20 20" aria-hidden="true"><path d="M5.2 2.5l2.6 3.3-1.7 2.1c.9 2 2.4 3.6 4.5 4.6l2-1.7 3.3 2.5-1.2 2.8c-6.3-.3-11.3-5.4-11.7-11.6z"/></svg>
            </span>
            <p class="contact-text">(+65) 8043 5617</p>
          </div>
          <div class="contact-item">
            <span class="contact-icon">
              <svg viewBox="0 0 20 20" aria-hidden="true"><path d="M2 5h16v1.2l-8 5-8-5z"/><path d="M2 8l8 5 8-5v7H2z"/></svg>
            </span>
            <p class="contact-text">marcus@kestreloak.com.sg</p>
          </div>
        </div>
      </div>
    </section>

    <section class="card card-front">
      <div class="card-red-field"></div>
      <div class="logo-band">
        <span class="brand-name">KestrelOak</span>
      </div>
    </section>
  </main>
</body>
</html>
```